CODED website - Breakfree418

I am a successful entrepreneur - have recently sold my business and am semi-retired. I want to give something back, as well as provide a blog for articles and my journeys.

I will also be using this to provide free business and entrepreneurial advice.

I am creating a NOT FOR PROFIT business called Breakfree418.com.au which will provide the following;

1. Blog and articles; my travels, Small to Medium business advice and articles

2. My Bucket List - the 100 things I aim to achieve

3. Free business / start up advice - a section on the website which provides case studies on people / businesses which ask me for advice. We will then chronicle their story and what advice we have given for them to succeed.

My inspiration is the Martin Oxendale idea and website;

http://martinoxendale.example/about-martin/

Obviously I do NOT want a copy of this site, but use this for inspiration.

Furthermore, I would be interested in ongoing collaboration with the successful designer - I will be providing advice and consultancy to start ups, all of which will need web design etc, so there is ongoing referral streams for the successful designer.

I need this to be CODED and then uplifted to the website, so please DO NOT bid on this unless you can provide a coded site and facilitate the upload to BrightHosting.

The NECESSARY tabs / pages

Main landing page - a short introduction into the ethos of Breakfree418

Writing - this will be the blog articles

About

Our Bucket List - a section where we can add our 100 buket list items. Hyperlinked to open a new page which has details on each bucket list item (ie #1 Make Breakfree418 - hyperlink to a new page which then has info on the bucklist item and what we have done)

Breakfree418 - this will be the section where we discuss people / businesses that we are helping. We will have an opening intro section + a link to the contact us page so they can ask us for the free advice. This will be the section where we have case studies into businesses / people that we have helped.

Hey everyone!

I'm really keen to get this website launched and looking amazing - if you have any questions, or would like to discuss anything at all, please email me at

dane@pollwick.example.com.au

As I mentioned in the brief, I am doing this site to give back; I will not be earning a cent, and I will not be trying to earn any funds. I'm doing it simply to help other start ups or entrepreneurs, so I really want this site to look amazing.

I hope someone reads this and is inspired, and wants to be involved in this social enterprise with me.

Really excited to hear from you all and see your designs!

Industry/Entity Type

Business

Requirements
Must have
• MUST BE CODED and uplifted to the BrightHosting registered domain - www.breakfree418.com.au - happy to discuss additional costings for this with successful designer.

Separate pages for each section (as outlined in the brief above)

Blog section to look similar to http://martinoxendale.example/3x5/

Comprehensive website - not a simple wordpress template theme with some minor modifications. I will immediately reject any simple template design. I am looking for a slick, fully functioning website design.

PLEASE BE AWARE that I am looking for ongoing collaboration with the www.breakfree418.com.au.

I am trying this website as I want to find a young, energetic, vibrant, dynamic designer - this is your opportunity to be a part of something big, as this website will be huge!

Please do not submit a design if you are not motivated and ready for something big.

```html
<!DOCTYPE html>
<html lang="en">
<head>
<meta charset="utf-8">
<title>Breakfree418</title>
<link rel="stylesheet" href="https://fonts.googleapis.com/css2?family=PT+Sans:wght@400;700&family=PT+Sans+Narrow:wght@700&display=swap">
<style>
:root{
  --page:#efefef;
  --white:#ffffff;
  --green:#1f7a3c;
  --green-dark:#17692f;
  --green-bright:#7ab43a;
  --green-btn:#4f9a2e;
  --ink:#333333;
  --muted:#8a8a8a;
  --red:#c0392b;
  --orange:#d9481c;
  --nav:#1d1d1d;
  --footer:#2a2a2a;
  --rule:#bdbdbd;
}
*{margin:0;padding:0;box-sizing:border-box}
html,body{width:778px;height:1200px;overflow:hidden}
body{background:var(--page);font-family:"PT Sans",Arial,sans-serif;color:var(--ink);position:relative}
.abs{position:absolute}
.sheet{left:24px;top:18px;width:730px;height:1114px;background:var(--white)}
.logo{left:54px;top:34px;font-size:30px;color:var(--green);letter-spacing:.3px;line-height:1}
.search{left:558px;top:32px;width:188px;height:17px;display:flex;box-shadow:0 4px 6px -4px rgba(0,0,0,.35)}
.search input{flex:1;border:1px solid #c9c9c9;height:17px;background:#fff}
.search button{width:47px;border:0;background:#8c8c8c;color:#fff;font:9px "PT Sans",sans-serif}
.nav{left:320px;top:64px;width:434px;height:35px;background:var(--nav);border-radius:0 6px 0 0;display:flex;align-items:center;justify-content:space-around;padding:0 6px}
.nav a{color:#fff;font-size:9.5px;text-decoration:none}
.nav a.current{color:#8bcf3f}
.hero{left:24px;top:100px;width:730px;height:295px;overflow:hidden}
.hero-photo{position:absolute;inset:0;background:linear-gradient(120deg,#3f6d86 0%,#5d7f62 30%,#4f6a30 55%,#6d6a52 80%,#8b8270 100%)}
.hero svg{position:absolute;left:0;top:0}
.hero h1{position:absolute;left:17px;top:57px;font-weight:400;font-size:17px;color:#fff}
.hero p{position:absolute;left:21px;top:98px;width:210px;font-size:9px;line-height:18px;color:#fff}
.learn{position:absolute;left:72px;top:194px;width:100px;height:28px;background:var(--green-dark);color:#fff;font:700 12px "PT Sans Narrow",sans-serif;display:flex;align-items:center;justify-content:center;border-radius:2px}
.dots{position:absolute;left:84px;top:251px;display:flex;gap:3px}
.dots i{width:7px;height:7px;border-radius:50%;background:#0e4a1d}
.dots i:first-child{background:#8bd04a}
h2.welcome{left:42px;top:415px;font-weight:400;font-size:15px;color:#333}
h2.welcome span{color:var(--orange)}
.rule{height:0;border-top:1px dotted var(--rule)}
.intro{left:44px;top:451px;width:450px;font-size:8px;line-height:15px;color:#555}
.intro p+p{margin-top:15px}
.more-link{color:var(--red);font-size:8.5px;text-decoration:none}
.section-title{font-weight:400;font-size:12.5px;color:var(--green)}
.card{width:149px;height:214px;background:#f7f7f7;box-shadow:0 1px 3px rgba(0,0,0,.3)}
.card .tag{height:25px;background:var(--green-bright);color:#fff;font-size:9.5px;padding:7px 12px}
.card .thumb{margin:5px 4px 0;height:78px}
.card p{margin:11px 4px 0;font-size:8px;line-height:15px;color:#555;text-align:justify}
.card .date{margin:10px 4px 0;font-size:8.5px;color:#555}
.card .view{position:absolute;right:8px;bottom:14px;color:var(--red);font-size:8.5px}
.box{width:216px;background:#f6f6f6;border:1px solid #dcdcdc;border-radius:4px;box-shadow:0 1px 3px rgba(0,0,0,.15)}
.box h3{position:absolute;left:50px;top:20px;font-weight:400;font-size:12.5px;color:#333}
.box .icon{position:absolute;left:12px;top:12px;width:30px;height:24px}
.box .line{position:absolute;left:12px;right:16px;top:40px;border-top:1px solid #cfcfcf}
.item{position:absolute;left:11px;width:200px}
.item .pic{position:absolute;left:0;top:0;width:56px;height:38px}
.item h4{position:absolute;left:63px;top:-1px;font-weight:400;font-size:9.5px;color:#222;white-space:nowrap}
.item p{position:absolute;left:64px;top:15px;width:138px;font-size:7.8px;line-height:13.5px;color:#9a9a9a}
.item .vm{position:absolute;right:1px;top:41px;font-size:7.5px;color:var(--red)}
.box .btn{position:absolute;right:0;bottom:0;width:75px;height:24px;background:var(--green-btn);color:#fff;font-size:10px;display:flex;align-items:center;justify-content:center;border-radius:0 0 3px 0}
.ethos{left:522px;top:932px;font-weight:400;font-size:13px;color:var(--green)}
.video{left:522px;top:963px;width:225px;height:130px;background:#111;border:2px solid #2b2b2b}
.video-still{position:absolute;left:0;top:0;right:0;bottom:14px;background:radial-gradient(ellipse at 50% 45%,#8a8a8a 0%,#4a4a4a 50%,#1e1e1e 100%)}
.play{position:absolute;left:98px;top:47px;width:26px;height:18px;background:#111;border-radius:3px}
.bar{position:absolute;left:0;right:0;bottom:0;height:14px;background:#1a1a1a}
.bar .track{position:absolute;left:4px;right:4px;top:1px;height:2px;background:#555}
.bar .track i{display:block;width:28%;height:2px;background:#cc2222}
.footer{left:0;top:1132px;width:778px;height:68px;background:var(--footer)}
.social{top:1158px;width:118px;height:20px;background:#2f8fc7;color:#fff;font-size:8px;display:flex;align-items:center;gap:8px;padding-left:4px;border-radius:2px}
.social i{width:13px;height:13px;background:#1f6f9f;border-radius:2px}
.social b{font-size:9.5px;font-weight:700}
.fnav{right:22px;top:1145px;font-size:8px;color:#ddd;white-space:nowrap}
.copy{right:22px;top:1166px;font-size:8px;color:#ccc}
</style>
</head>
<body>
<div class="abs sheet"></div>

<div class="abs logo">Breakfree418</div>
<form class="abs search"><input type="text" aria-label="Search"><button type="button">SEARCH</button></form>
<nav class="abs nav">
  <a class="current" href="#">HOME</a><a href="#">ABOUT US</a><a href="#">PLACES</a><a href="#">ARTICLES</a><a href="#">ADVICES</a><a href="#">BLOG</a><a href="#">CONTACT US</a>
</nav>

<section class="abs hero">
  <div class="hero-photo" role="img" aria-label="Hiker with a backpack on a rocky green coastal cliff above the sea"></div>
  <svg width="730" height="295" viewBox="0 0 730 295">
    <defs><linearGradient id="heroGreen" x1="0" y1="0" x2="0" y2="1"><stop offset="0" stop-color="#6fb13a"/><stop offset="1" stop-color="#1f8a36"/></linearGradient></defs>
    <polygon points="0,0 284,0 184,295 0,295" fill="url(#heroGreen)"/>
    <polygon points="284,0 290,0 190,295 184,295" fill="#a9d66a" opacity=".8"/>
  </svg>
  <h1>Proin dui lectus mattis laoreet</h1>
  <p>Proin dui lectus, cursus eu, mattis laoreet, viverra sit amet, quam. Curabitur vel dolor ultrices ipsum dictum tristique. Praesent vitae lacus. Ut velit enim, vestibulum non, fermentum nec.</p>
  <div class="learn">LEARN MORE</div>
  <div class="dots"><i></i><i></i><i></i><i></i></div>
</section>

<h2 class="abs welcome">Welcome to <span>Breakfree418</span></h2>
<div class="abs rule" style="left:44px;top:441px;width:410px"></div>
<div class="abs intro">
  <p>Sed ut perspiciatis unde omnis iste natus error sit voluptatem accusantium doloremque laudantium, totam rem aperiam, eaque ipsa quae ab illo inventore veritatis et quasi architecto beatae vitae dicta sunt explicabo. Sed ut perspiciatis unde omnis iste natus error sit voluptatem accusantium doloremque laudantium, totam rem aperiam, eaque ipsa quae ab illo inventore veritatis et quasi architecto beatae vitae dicta sunt explicabo.</p>
  <p>Sed ut perspiciatis unde omnis iste natus error sit voluptatem accusantium doloremque laudantium, totam rem aperiam, eaque ipsa quae ab illo inventore veritatis et quasi architecto beatae vitae dicta sunt explicabo.</p>
</div>
<a class="abs more-link" style="left:450px;top:566px" href="#">MORE &nbsp;&gt;&gt;</a>

<h3 class="abs section-title" style="left:41px;top:584px">LATEST ARTICLES</h3>
<div class="abs rule" style="left:41px;top:603px;width:412px"></div>

<article class="abs card" style="left:35px;top:618px"><div class="tag">TRAVEL</div><div class="thumb" role="img" aria-label="Smiling traveller beside a pink car by the sea" style="background:linear-gradient(#7fc6e8,#e4b6c8)"></div><p>Sed ut perspiciatis unde omnis iste natus error sit voluptatem accusantium doloremque laudantium.</p><div class="date">Dec 28,2012</div><span class="view">VIEW MORE &nbsp;&gt;&gt;</span></article>
<article class="abs card" style="left:197px;top:618px"><div class="tag">TRAVEL</div><div class="thumb" role="img" aria-label="Group planning a trip over maps at a table" style="background:linear-gradient(#b9aa9a,#6d5a4c)"></div><p>Sed ut perspiciatis unde omnis iste natus error sit voluptatem accusantium doloremque laudantium.</p><div class="date">Dec 28,2012</div><span class="view">VIEW MORE &nbsp;&gt;&gt;</span></article>
<article class="abs card" style="left:358px;top:618px"><div class="tag">TRAVEL</div><div class="thumb" role="img" aria-label="Traveller with luggage reading a map on the floor" style="background:linear-gradient(#f2f2f2,#c7bfb4)"></div><p>Sed ut perspiciatis unde omnis iste natus error sit voluptatem accusantium doloremque laudantium.</p><div class="date">Dec 28,2012</div><span class="view">VIEW MORE &nbsp;&gt;&gt;</span></article>

<h3 class="abs section-title" style="left:41px;top:851px">BUSINESS ARTICLES</h3>
<div class="abs rule" style="left:41px;top:870px;width:412px"></div>

<article class="abs card" style="left:35px;top:881px"><div class="tag">BUSINESS</div><div class="thumb" role="img" aria-label="Hands writing notes next to a laptop keyboard" style="background:linear-gradient(#f4f4f4,#bdbdbd)"></div><p>Sed ut perspiciatis unde omnis iste natus error sit voluptatem accusantium doloremque laudantium.</p><div class="date">Dec 28,2012</div><span class="view">VIEW MORE &nbsp;&gt;&gt;</span></article>
<article class="abs card" style="left:198px;top:881px"><div class="tag">BUSINESS</div><div class="thumb" role="img" aria-label="Two colleagues working together at a laptop" style="background:linear-gradient(#f4f4f4,#9c9a9a)"></div><p>Sed ut perspiciatis unde omnis iste natus error sit voluptatem accusantium doloremque laudantium.</p><div class="date">Dec 28,2012</div><span class="view">VIEW MORE &nbsp;&gt;&gt;</span></article>
<article class="abs card" style="left:359px;top:881px"><div class="tag">BUSINESS</div><div class="thumb" role="img" aria-label="Business team standing in a row" style="background:linear-gradient(#eef0f3,#2f3a52)"></div><p>Sed ut perspiciatis unde omnis iste natus error sit voluptatem accusantium doloremque laudantium.</p><div class="date">Dec 28,2012</div><span class="view">VIEW MORE &nbsp;&gt;&gt;</span></article>

<aside class="abs box" style="left:522px;top:414px;height:244px">
  <svg class="icon" viewBox="0 0 30 24" aria-hidden="true"><rect x="2" y="7" width="20" height="14" fill="#fff" stroke="#999" transform="rotate(-10 12 14)"/><line x1="6" y1="13" x2="17" y2="11" stroke="#aaa"/><line x1="6" y1="16" x2="17" y2="14" stroke="#aaa"/><rect x="18" y="2" width="4" height="16" fill="#e2a33a" transform="rotate(45 20 10)"/></svg>
  <h3>MY BUCKET LIST</h3><div class="line"></div>
  <div class="item" style="top:52px"><div class="pic" role="img" aria-label="White sand beach with turquoise water" style="background:linear-gradient(#5fa6d1,#e8e4d2)"></div><h4>Sed ut perspiciatis unde omnis</h4><p>Sed ut perspiciatis unde omnis iste natus error voluptatem laudantium,</p></div>
  <div class="item" style="top:108px"><div class="pic" role="img" aria-label="Beach umbrella on a tropical shore" style="background:linear-gradient(#8fc9e6,#1f7fb0)"></div><h4 style="left:65px">Sed ut perspiciatis unde omnis</h4><p style="left:66px">Sed ut perspiciatis unde omnis iste natus error voluptatem laudantium,</p></div>
  <div class="item" style="top:168px"><div class="pic" role="img" aria-label="Couple outdoors in warm light" style="background:linear-gradient(#c98a3c,#3d5a22)"></div><h4 style="left:65px">Sed ut perspiciatis unde omnis</h4><p style="left:66px">Sed ut perspiciatis unde omnis iste natus error voluptatem laudantium,</p></div>
  <div class="btn">MORE</div>
</aside>

<aside class="abs box" style="left:522px;top:676px;height:244px">
  <svg class="icon" viewBox="0 0 30 24" aria-hidden="true"><rect x="4" y="4" width="20" height="16" fill="#fff" stroke="#999" transform="rotate(-8 14 12)"/><rect x="7" y="6" width="20" height="16" fill="#fafafa" stroke="#888" transform="rotate(6 17 14)"/><line x1="10" y1="12" x2="23" y2="13" stroke="#aaa"/><line x1="10" y1="16" x2="23" y2="17" stroke="#aaa"/></svg>
  <h3>TOP ARTICLES</h3><div class="line"></div>
  <div class="item" style="top:54px"><div class="pic" role="img" aria-label="Kayak on a blue bay below cliffs" style="background:linear-gradient(#c7a88a,#2c86b8)"></div><h4>Sed ut perspiciatis unde omnis</h4><p>Sed ut perspiciatis unde omnis iste natus error voluptatem laudantium,</p><span class="vm">VIEW MORE &gt;&gt;</span></div>
  <div class="item" style="top:110px"><div class="pic" role="img" aria-label="Rider on horseback on a rocky trail" style="background:linear-gradient(#8a7c68,#3e3a30)"></div><h4 style="left:65px">Sed ut perspiciatis unde omnis</h4><p style="left:66px">Sed ut perspiciatis unde omnis iste natus error voluptatem laudantium,</p><span class="vm">VIEW MORE &gt;&gt;</span></div>
  <div class="item" style="top:169px"><div class="pic" role="img" aria-label="Skier on a snowy slope under blue sky" style="background:linear-gradient(#2e5f9e,#e8eef3)"></div><h4 style="left:65px">Sed ut perspiciatis unde omnis</h4><p style="left:66px">Sed ut perspiciatis unde omnis iste natus error voluptatem laudantium,</p><span class="vm">VIEW MORE &gt;&gt;</span></div>
  <div class="btn">MORE</div>
</aside>

<h3 class="abs ethos">Ethos of Breakfree418</h3>
<div class="abs rule" style="left:522px;top:952px;width:204px"></div>
<div class="abs video">
  <div class="video-still" role="img" aria-label="Open book with fanned pages, video still"></div>
  <div class="play"><svg width="26" height="18" viewBox="0 0 26 18"><polygon points="10,4 18,9 10,14" fill="#fff"/></svg></div>
  <div class="bar"><div class="track"><i></i></div></div>
</div>

<footer class="abs footer"></footer>
<div class="abs social" style="left:41px"><i></i><span>Follow us on <b>Chirpline</b></span></div>
<div class="abs social" style="left:172px"><i></i><span>Find us on <b>Friendspace</b></span></div>
<div class="abs fnav">Home &nbsp;| &nbsp;About us &nbsp;| &nbsp;Places| &nbsp;Articles &nbsp;| &nbsp;Advises &nbsp;| Blog &nbsp;| &nbsp;Contact Us</div>
<div class="abs copy">Copyright © 2012 breakfree418.com, &nbsp;All rights reserved.</div>
</body>
</html>
```